New business card/stationary for a consulting company

I am looking for a clean and very professional looking business card for my consulting company as well as corresponding stationary. I am uploading our logo. I like simple and powerful for the feel. No graphics but I am open on everything else. Below is my contact information but would like the final to be in a version I can add my employees information into and print. Thank you.

Daniel Whitcombe
dan@ferncliffadvisory.com
2870 North 9th Avenue, Summit Floor, Elm Ridge, Illinois 60531
www.ferncliffadvisory.com

Industry/Entity Type

Consulting

Contact Information for Business Card

Daniel Whitcombe
dan@ferncliffadvisory.com
www.ferncliffadvisory.com

Font styles to use
Serif
Sans Serif

Requirements
Must have
• Our logo and the business card details.
Nice to have
• our website www.ferncliffadvisory.com

```html
<!DOCTYPE html>
<html lang="en">
<head>
<meta charset="utf-8">
<title>Ferncliff Advisory – Business Card</title>
<link rel="stylesheet" href="https://fonts.googleapis.com/css2?family=Cinzel:wght@700&family=Montserrat:wght@400&family=Roboto:wght@400&display=swap">
<style>
  :root {
    --backdrop: #e9e6e2;
    --card-white: #f7f7f7;
    --navy: #0a0a78;
    --navy-bright: #0a0a9c;
    --navy-deep: #020260;
    --band-grey: #b4b4b4;
    --text-grey: #555555;
    --divider: #c8c8c8;
    --white: #ffffff;
  }
  * { margin: 0; padding: 0; box-sizing: border-box; }
  html, body {
    width: 1200px; height: 960px; overflow: hidden;
    background: var(--backdrop);
  }
  .stage { position: relative; width: 1200px; height: 960px; }

  .card { position: absolute; width: 600px; box-shadow: 0 2px 6px rgba(0,0,0,.25); }

  /* Front */
  .card--front {
    left: 302px; top: 129px; height: 342px;
    background: var(--card-white);
  }
  .brand {
    display: flex; align-items: center; gap: 10px;
    font-family: "Montserrat", sans-serif; font-weight: 400;
    letter-spacing: 0.5px; white-space: nowrap;
  }
  .brand__square { display: block; flex: none; }
  .card--front .brand {
    position: absolute; left: 38px; top: 184px;
    color: var(--navy); font-size: 17px;
  }
  .card--front .brand__square { width: 16px; height: 16px; background: var(--navy); }
  .divider {
    position: absolute; left: 316px; top: 106px;
    width: 1px; height: 136px;
    background: linear-gradient(to bottom, transparent, var(--divider) 20%, var(--divider) 80%, transparent);
  }
  .contact { position: absolute; left: 345px; top: 104px; }
  .contact__name {
    font-family: "Cinzel", serif; font-weight: 700;
    font-size: 17px; color: var(--navy); letter-spacing: 0.6px;
    margin-bottom: 10px;
  }
  .contact__address, .contact__line {
    font-family: "Roboto", sans-serif; font-size: 14px;
    line-height: 18px; color: var(--text-grey);
  }
  .contact__address { margin-bottom: 10px; }
  .contact__line { display: flex; align-items: center; gap: 6px; }
  .contact__icon { width: 13px; height: 13px; flex: none; }
  .band { position: absolute; left: 0; bottom: 0; width: 600px; height: 15px; }

  /* Back */
  .card--back {
    left: 299px; top: 488px; height: 343px;
    background: linear-gradient(100deg, var(--navy-bright) 0%, var(--navy) 55%, var(--navy-deep) 100%);
    display: flex; align-items: center; justify-content: center;
  }
  .card--back .brand { color: var(--white); font-size: 30px; gap: 16px; }
  .card--back .brand__square { width: 28px; height: 28px; background: var(--white); }
</style>
</head>
<body>
<main class="stage">
  <section class="card card--front" aria-label="Business card front">
    <div class="brand">
      <span class="brand__square"></span>
      <span class="brand__name">FERNCLIFF ADVISORY</span>
    </div>
    <div class="divider"></div>
    <div class="contact">
      <p class="contact__name">Daniel Whitcombe</p>
      <p class="contact__address">2870 North 9th Avenue<br>Summit Floor, Elm Ridge<br>Illinois 60531</p>
      <p class="contact__line">
        <svg class="contact__icon" viewBox="0 0 13 13" aria-hidden="true">
          <rect x="1" y="3" width="11" height="7.5" fill="var(--navy)"/>
          <polyline points="1,3.3 6.5,7.3 12,3.3" fill="none" stroke="var(--card-white)" stroke-width="1"/>
        </svg>
        dan@ferncliffadvisory.com
      </p>
      <p class="contact__line">
        <svg class="contact__icon" viewBox="0 0 13 13" aria-hidden="true">
          <circle cx="6.5" cy="6.5" r="6" fill="var(--navy)"/>
          <ellipse cx="6.5" cy="6.5" rx="2.5" ry="6" fill="none" stroke="var(--card-white)" stroke-width="0.8"/>
          <line x1="0.5" y1="6.5" x2="12.5" y2="6.5" stroke="var(--card-white)" stroke-width="0.8"/>
        </svg>
        www.ferncliffadvisory.com
      </p>
    </div>
    <svg class="band" viewBox="0 0 600 15" preserveAspectRatio="none" aria-hidden="true">
      <polygon points="0,0 393,0 388,15 0,15" fill="var(--navy)"/>
      <polygon points="393,0 395,0 390,15 388,15" fill="var(--white)"/>
      <polygon points="395,0 600,0 600,15 390,15" fill="var(--band-grey)"/>
    </svg>
  </section>

  <section class="card card--back" aria-label="Business card back">
    <div class="brand">
      <span class="brand__square"></span>
      <span class="brand__name">FERNCLIFF ADVISORY</span>
    </div>
  </section>
</main>
</body>
</html>
```